R7M Horizon Business Card Design

We need a business card created for our New Business "R7M Horizon"<br/><br/>The business card design is up to you however the following information must be on the business card:<br/><br/>Front of the business card -<br/>Email :darrenp@r7mhorizon.nz<br/>Mobile: +64 (0) 22 4870 619<br/>Website: www.r7mhorizon.nz<br/>Card Owner Name: Darren Paltrow<br/>Company Title: Business Development Manager<br/>Slogan: "The BEST of both worlds". <br/>Logo On the front attached to the design brief<br/><br/>On the back: <br/>Space on the back for 4 more versions of the logo across the bottom of the card indicating different subsidiary brands - R7M Coffee, R7M Arts, R7M ?? (The card will be used for all of these brands - We Will add the extra subsidiary logos to the design once the design is finished (We are a graphics design team). <br/><br/>Other than that we want a premium feeling logo that remains universally usable depending on the business entity that we are using the card for. The use of bright bold colours would be great but we still want the card to feel premium.
Target Market(s)
Gift Design and Manufacturing Companies
Contact Information for Business Card
Front of the business card -
Email :darrenp@r7mhorizon.nz
Mobile: +64 (0) 22 4870 619
Website: www.r7mhorizon.nz
Card Owner Name: Darren Paltrow
Company Title: Business Development Manager
Slogan: "The BEST of both worlds".
Logo On the front attached to the design brief

```html
<!DOCTYPE html>
<html lang="en">
<head>
<meta charset="utf-8">
<title>R7M Horizon – Business Card</title>
<link href="https://fonts.googleapis.com/css2?family=Open+Sans:wght@400;600;700&family=Syncopate:wght@700&display=swap" rel="stylesheet">
<style>
  :root {
    --bg: #5a5a5a;
    --card-dark: #111111;
    --card-light: #ffffff;
    --brand-blue: #2b3a9e;
    --ink: #2a2a2a;
    --ink-soft: #444444;
    --white: #ffffff;
  }
  * { box-sizing: border-box; margin: 0; padding: 0; }
  html, body {
    width: 1200px; height: 900px; overflow: hidden;
    background: var(--bg);
    font-family: "Open Sans", Arial, sans-serif;
  }
  .stage {
    width: 1200px; height: 900px;
    display: flex; align-items: center; justify-content: center; gap: 40px;
  }
  .card {
    position: relative;
    width: 540px; height: 310px;
    border-radius: 26px;
    overflow: hidden;
  }

  /* Back side */
  .card--back { background: var(--card-dark); color: var(--white); }
  .back__brand {
    position: absolute; left: 0; right: 0; top: 96px;
    text-align: center;
  }
  .brand-name {
    font-family: "Open Sans", Arial, sans-serif;
    font-weight: 700; font-size: 40px; letter-spacing: 0.5px;
    white-space: nowrap;
  }
  .back__slogan {
    position: absolute; left: 0; right: 0; bottom: 48px;
    display: flex; align-items: center; justify-content: center; gap: 8px;
    font-size: 14px;
  }
  .back__slogan svg { width: 8px; height: 8px; fill: var(--white); }

  /* Front side */
  .card--front { background: var(--card-light); color: var(--ink); }
  .front__brand {
    position: absolute; left: 34px; top: 28px;
    color: var(--brand-blue);
  }
  .front__brand .brand-name { font-size: 28px; }
  .person { position: absolute; left: 34px; top: 100px; }
  .person__name {
    font-family: "Syncopate", "Arial Black", sans-serif;
    font-weight: 700; font-size: 20px; color: var(--brand-blue);
    text-transform: uppercase; letter-spacing: 0.5px;
    white-space: nowrap;
  }
  .person__title { font-size: 14px; color: var(--ink-soft); margin-top: 4px; }
  .divider {
    position: absolute; left: 34px; right: 34px; top: 176px;
    height: 1px; background: var(--brand-blue);
  }
  .contact-list {
    position: absolute; left: 34px; top: 192px;
    list-style: none; font-size: 13.5px; color: var(--ink); line-height: 24px;
  }
  .contact-list li { display: flex; align-items: center; gap: 10px; white-space: nowrap; }
  .contact-list svg { width: 12px; height: 12px; fill: var(--brand-blue); flex: none; }
  .front__slogan {
    position: absolute; right: 34px; top: 196px;
    font-size: 14px; color: var(--brand-blue);
    padding-bottom: 6px; border-bottom: 2px solid var(--brand-blue);
    white-space: nowrap;
  }
  strong { font-weight: 700; }
</style>
</head>
<body>
<main class="stage">

  <section class="card card--back" aria-label="Card back">
    <div class="back__brand">
      <span class="brand-name">R7M Horizon</span>
    </div>
    <p class="back__slogan">
      <svg viewBox="0 0 8 8" aria-hidden="true"><polygon points="8,0 8,8 0,4"/></svg>
      <span>The <strong>BEST</strong> of both worlds</span>
      <svg viewBox="0 0 8 8" aria-hidden="true"><polygon points="0,0 8,4 0,8"/></svg>
    </p>
  </section>

  <section class="card card--front" aria-label="Card front">
    <div class="front__brand">
      <span class="brand-name">R7M Horizon</span>
    </div>
    <div class="person">
      <h1 class="person__name">Darren Paltrow</h1>
      <p class="person__title">Business Development Manager</p>
    </div>
    <div class="divider"></div>
    <ul class="contact-list">
      <li>
        <svg viewBox="0 0 12 12" aria-hidden="true"><path d="M2.5 0.5l2 2.4-1.2 1.4c.7 1.6 2 2.9 3.6 3.6l1.4-1.2 2.4 2-1.1 2.1C5.6 10.6 1.4 6.4 0.6 2z"/></svg>
        +64 (0) 22 4870 619
      </li>
      <li>
        <svg viewBox="0 0 12 12" aria-hidden="true"><path d="M0 2h12v8H0z M1.2 3.2v5.6h9.6V3.2L6 6.6z M1.8 3L6 5.8 10.2 3z" fill-rule="evenodd"/></svg>
        darrenp@r7mhorizon.nz
      </li>
      <li>
        <svg viewBox="0 0 12 12" aria-hidden="true"><circle cx="6" cy="6" r="6"/><path d="M0 6h12M6 0v12" stroke="#fff" stroke-width="0.8"/></svg>
        www.r7mhorizon.nz
      </li>
    </ul>
    <p class="front__slogan">The <strong>BEST</strong> of both worlds</p>
  </section>

</main>
</body>
</html>
```